International business needs business cards

Our company, DRV Ventures Inc. is in the business of supplying a range construction products with particular emphasis on CEMENT. We have developed our own brand - TORVAN SUPPLIES - with which to infiltrate the market. We are launching our brand of cement (TORVAN Type IS Cement) into the Caribbean which is unlike anything this market has ever seen. A monopoly has existed here for the past 60-odd years and the market has now opened to allow the importation of other brands and consumers are anxious and ready for change/improvement. We are very excited to be launching and want to make a great first impression. We will be conducting workshops and seminars (from government level to the hardware store owners) and we want our business card to give us the strong, confident introduction that we need.

Target Market(s)

construction; builders; engineers; home owners

Industry/Entity Type

Construction

Contact Information for Business Card

Marisol Depree
CEO
cell # 1 555 4180736
Ground floor,Lindell Plaza Suite 2734
George Town,Grand Cayman
Cayman Islands,KY1-4823
EMAIL: m.depree@drvventuresinc.example
web site drvventuresinc.example

COMPANY: skype info drv.ventures.example

second card
Yvette Brannock-Depree
CFO
CELL# 1 555 607 3941
George Town,Grand Cayman
Cayman Islands,KY1-4823
EMAIL: y.brannockdepree@drvventuresinc.example
website drvventuresinc.example

Requirements
Must have
• Business cards must display BOTH logos - DRV is the company and TORVAN is the brand.

```html
<!DOCTYPE html>
<html lang="en">
<head>
<meta charset="utf-8">
<title>DRV Ventures Inc. – Business Cards</title>
<link rel="stylesheet" href="https://fonts.googleapis.com/css2?family=Open+Sans:wght@400;600;700&display=swap">
<style>
  :root {
    --stage: #2e2e2e;
    --card-dark: #050505;
    --card-light: #ffffff;
    --ink: #111111;
    --brand-red: #8b1a1f;
    --accent-red: #c0272d;
    --silver: #b9b9b9;
    --muted: #d6d6d6;
  }
  * { margin: 0; padding: 0; box-sizing: border-box; }
  html, body {
    width: 1200px; height: 900px; overflow: hidden;
    background: var(--stage);
    font-family: "Open Sans", Arial, sans-serif;
  }
  .canvas { position: relative; width: 1200px; height: 900px; }

  .card {
    position: absolute; width: 700px; height: 400px;
    box-shadow: 0 10px 30px rgba(0,0,0,.45);
  }

  /* Back of card: brand side */
  .card--brand { left: 60px; top: 40px; background: var(--card-dark); color: var(--muted); }
  .brand-mark {
    position: absolute; left: 0; right: 0; top: 120px;
    display: flex; align-items: center; justify-content: center; gap: 16px;
  }
  .brand-mark__square { width: 34px; height: 34px; background: var(--silver); }
  .brand-mark__name {
    font-weight: 700; font-size: 64px; letter-spacing: 6px; color: var(--silver);
  }
  .brand-handle {
    position: absolute; left: 0; right: 0; top: 300px;
    display: flex; align-items: center; justify-content: center; gap: 10px;
    font-size: 22px; color: #ececec;
  }
  .brand-handle__dot { width: 18px; height: 18px; border-radius: 50%; background: #ececec; }

  /* Front of card: contact side */
  .card--contact { left: 440px; top: 470px; background: var(--card-light); color: var(--ink); }
  .company-mark {
    position: absolute; left: 150px; top: 50px;
    display: flex; align-items: center; gap: 18px;
  }
  .company-mark__square { width: 120px; height: 120px; background: var(--brand-red); }
  .company-mark__name { font-weight: 700; font-size: 40px; line-height: 1.05; color: var(--ink); }

  .person { position: absolute; left: 300px; top: 200px; text-align: center; }
  .person__name { font-weight: 700; font-size: 28px; letter-spacing: .5px; }
  .person__role { font-size: 15px; color: var(--accent-red); margin-top: -2px; }

  .address {
    position: absolute; left: 36px; top: 290px;
    font-size: 16px; font-weight: 600; line-height: 1.3; text-align: right;
  }
  .contact-list {
    position: absolute; left: 370px; top: 282px;
    list-style: none; font-size: 16px; line-height: 1.35;
  }
  .contact-list li { display: flex; align-items: center; gap: 8px; }
  .contact-list svg { width: 14px; height: 14px; flex: none; }
</style>
</head>
<body>
<main class="canvas">

  <section class="card card--brand" aria-label="Business card back">
    <div class="brand-mark">
      <span class="brand-mark__square"></span>
      <span class="brand-mark__name">TORVAN</span>
    </div>
    <div class="brand-handle">
      <span class="brand-handle__dot"></span>
      <span>drv.ventures.example</span>
    </div>
  </section>

  <section class="card card--contact" aria-label="Business card front">
    <div class="company-mark">
      <span class="company-mark__square"></span>
      <span class="company-mark__name">DRV Ventures Inc.</span>
    </div>

    <div class="person">
      <p class="person__name">MARISOL DEPREE</p>
      <p class="person__role">CEO</p>
    </div>

    <address class="address" style="font-style:normal">
      Ground floor,Lindell Plaza Suite 2734<br>
      George Town,Grand Cayman<br>
      Cayman Islands,KY1-4823
    </address>

    <ul class="contact-list">
      <li>
        <svg viewBox="0 0 24 24" aria-hidden="true"><path fill="#c0272d" d="M6.6 10.8a15.1 15.1 0 0 0 6.6 6.6l2.2-2.2a1 1 0 0 1 1-.25 11.4 11.4 0 0 0 3.6.57 1 1 0 0 1 1 1V20a1 1 0 0 1-1 1A17 17 0 0 1 3 4a1 1 0 0 1 1-1h3.5a1 1 0 0 1 1 1c0 1.25.2 2.45.57 3.57a1 1 0 0 1-.25 1z"/></svg>
        <span>1 555 4180736</span>
      </li>
      <li>
        <svg viewBox="0 0 24 24" aria-hidden="true"><rect x="3" y="5" width="18" height="14" fill="none" stroke="#c0272d" stroke-width="2"/><path d="M3 6l9 7 9-7" fill="none" stroke="#c0272d" stroke-width="2"/></svg>
        <span>m.depree@drvventuresinc.example</span>
      </li>
      <li>
        <svg viewBox="0 0 24 24" aria-hidden="true"><g fill="none" stroke="#c0272d" stroke-width="2"><circle cx="12" cy="12" r="9"/><ellipse cx="12" cy="12" rx="4" ry="9"/><path d="M3 12h18"/></g></svg>
        <span>www.drvventuresinc.example</span>
      </li>
    </ul>
  </section>

</main>
</body>
</html>
```